Willow Brook Paddock Refuge - Sponsorship Flyer

We require an A4 trifold flyer. Our colours are orange, black and white.
At The Willow Brook Paddock Refuge, we have a number of our animals available for Sponsorship. The majority are horses or ponies reflecting our focus however from time to time other animals in need find the peace of our Sanctuary.

Your sponsorship donation helps with the cost of care for horses requiring long-term rehabilitation including ongoing vet care etc as more often than not, the horse will have arrived in poor condition.

For those horses that are unsound or aged, (but with quality of life) and therefore not suited for adoption, are allowed to live out their days here at the Sanctuary.

As a DGR* charity all donations over $2 are tax deductible.

We have two different sponsorship types…Keepers of WBPR and Allies of WBPR

Target Market(s)

Horse Lovers

Industry/Entity Type

Rescue

Font styles to use
Serif

Colors
EE7325
F08F49
F5BC92
FAE3D3
FDF4ED

Requirements
Must have
• KEEPERS of WBPR Store/SPONSORSHIP/KEEPERS of WBPR Our Guardian sponsors choose to be with us for the long term. Their regular donation helps cover the monthly costs involved with caring for our residents. We like to think of these special folk as Guardian Angels. Their generosity allows us to keep so many safe from harm in this magical place. Guardian Sponsors receive a personalised e-certificate as well as a six-monthly update. We also invite our Guardians to contact us to organise a visit to the Sanctuary at a mutually convenient time. Here, you can meet the horse or pony that has captured your heart. Sponsorship costs vary from $15 – $25 per week depending on the animal and its needs.
Should not have
• External sourced photos

```html
<!DOCTYPE html>
<html lang="en">
<head>
<meta charset="utf-8">
<title>Willow Brook Paddock Refuge – Sponsorship Flyer</title>
<link rel="stylesheet" href="https://fonts.googleapis.com/css2?family=Gilda+Display&family=Nunito+Sans:wght@300;400&display=swap">
<style>
:root{
  --orange:#EE7325;
  --orange-mid:#F08F49;
  --orange-soft:#F5BC92;
  --peach:#FAE3D3;
  --cream:#FDF4ED;
  --paper:#ECE6DB;
  --ink:#1d1a17;
  --brown:#7A4A2E;
  --white:#ffffff;
  --bg:#e4e4e2;
  --serif:"Gilda Display", Georgia, serif;
  --sans:"Nunito Sans", Arial, sans-serif;
}
*{box-sizing:border-box;margin:0;padding:0}
html,body{width:1200px;height:1200px;overflow:hidden;background:var(--bg)}
.canvas{position:relative;width:1200px;height:1200px}
.sheet{position:absolute;left:209px;width:781px;height:560px;overflow:hidden;box-shadow:0 2px 8px rgba(0,0,0,.18)}
.sheet--outside{top:25px}
.sheet--inside{top:615px}
.panel{position:absolute;top:0;width:261px;height:560px}
.panel--left{left:0}.panel--mid{left:261px;width:259px}.panel--right{left:520px}
.abs{position:absolute}
.photo{position:absolute}

/* wordmark */
.wordmark{position:absolute;display:flex;align-items:center;gap:6px;font-family:var(--serif);line-height:1.05;text-align:right}
.wordmark__name{font-size:13px}
.wordmark__square{width:30px;height:44px;flex:none}
.wordmark--white{color:var(--white)}.wordmark--white .wordmark__square{background:var(--white)}
.wordmark--orange{color:var(--orange)}.wordmark--orange .wordmark__square{background:var(--orange)}

/* outside */
.about{background:var(--orange-mid);height:329px;color:var(--cream)}
.about__title{position:absolute;left:29px;top:100px;font-family:var(--serif);font-size:16px;color:var(--ink)}
.about__rule{position:absolute;left:29px;top:123px;width:198px;height:1px;background:var(--ink)}
.about__body{position:absolute;left:29px;top:136px;width:195px;font-family:var(--sans);font-weight:300;font-size:9px;line-height:12px;color:var(--cream)}
.about__addr{position:absolute;left:29px;top:243px;font-family:var(--sans);font-weight:300;font-size:9.5px;display:flex;gap:6px;align-items:center;color:var(--cream)}
.about__dgr{position:absolute;left:29px;top:288px;font-family:var(--sans);font-weight:300;font-size:8.5px;line-height:12px;color:var(--peach)}

.herd{left:0;top:329px;width:520px;height:231px;background:linear-gradient(180deg,#c9d1d6 0%,#6f7a4a 18%,#4f5e33 42%,#8a7048 62%,#a39a62 82%,#8c8a52 100%)}

.contact{background:linear-gradient(180deg,#ebe5d9 0%,#e3dccd 100%);height:329px}
.contact__title{position:absolute;left:33px;top:32px;font-family:var(--serif);font-size:18px;color:var(--orange)}
.contact__intro{position:absolute;left:33px;top:70px;width:170px;font-family:var(--sans);font-weight:300;font-size:9.5px;line-height:13px;color:var(--ink)}
.contact__intro span{color:var(--orange-mid)}
.contact__label{position:absolute;left:33px;top:136px;font-family:var(--sans);font-size:11px;color:var(--ink)}
.contact__list{position:absolute;left:33px;top:155px;list-style:none;font-family:var(--sans);font-weight:300;font-size:10px;color:#3a3530}
.contact__list li{display:flex;align-items:center;gap:7px;height:19px}
.pony{left:158px;top:148px;width:101px;height:181px;background:radial-gradient(ellipse at 55% 45%,#b27a4d 0%,#c89a72 40%,rgba(227,220,205,0) 75%)}

.cover{background:linear-gradient(180deg,#3f86c7 0%,#78aedb 30%,#a9c9e4 45%,#5c6a5c 60%,#55733f 100%)}
.cover__title{position:absolute;left:17px;top:40px;font-family:var(--serif);font-size:38px;line-height:38px;color:var(--ink)}
.cover__rule{position:absolute;left:17px;top:130px;width:216px;height:1px;background:var(--ink)}
.cover__text{position:absolute;left:17px;top:140px;width:220px;font-family:var(--sans);font-size:9.8px;line-height:12px;color:var(--ink)}
.mares{left:0;top:235px;width:261px;height:325px;background:linear-gradient(160deg,rgba(110,70,40,.0) 0%,#6b4127 25%,#5a3620 55%,#7a6a9a 75%,#4d6b36 100%)}

/* inside */
.donkey{left:0;top:0;width:261px;height:392px;background:linear-gradient(100deg,#6f7a52 0%,#8a8070 35%,#b9b4ad 55%,#8a4a35 78%,#5c3a2a 100%)}
.saves{position:absolute;left:0;top:392px;width:261px;height:168px;background:var(--orange-mid)}
.saves__title{position:absolute;left:20px;top:20px;font-family:var(--serif);font-size:16px;color:var(--ink)}
.saves__body{position:absolute;left:22px;top:48px;width:212px;font-family:var(--sans);font-weight:300;font-size:8px;line-height:11px;color:var(--cream)}
.saves__body p+p{margin-top:9px}

.tier__head{position:absolute;left:0;top:0;width:100%;height:103px}
.tier__head--keepers{background:linear-gradient(90deg,#EDA552 0%,#EE9A48 100%)}
.tier__head--allies{background:linear-gradient(90deg,#EE9245 0%,#EE7325 100%)}
.tier__icon{position:absolute;left:19px;top:21px;width:66px;height:66px;border-radius:50%;border:3px solid var(--brown);background:rgba(122,74,46,.15)}
.tier__title{position:absolute;left:95px;top:29px;font-family:var(--serif);font-size:17px;color:var(--ink);white-space:nowrap}
.tier__rule{position:absolute;left:95px;top:55px;width:147px;height:1px;background:var(--ink)}
.tier__sub{position:absolute;left:96px;top:60px;width:150px;font-family:var(--sans);font-size:8.6px;line-height:12px;color:var(--ink)}
.tier__body{position:absolute;left:0;top:103px;width:100%;height:457px;background:linear-gradient(180deg,#ebe5d9,#e4ddcf)}
.tier__list{position:absolute;left:20px;top:24px;list-style:none;font-family:var(--sans);font-weight:300;font-size:8.6px;line-height:12px;color:#2e2a26}
.tier__list li{position:relative;padding-left:8px;margin-bottom:12px}
.tier__list li::before{content:"•";position:absolute;left:0}
.tier__note{position:absolute;left:28px;top:246px;width:190px;font-family:var(--sans);font-size:8.6px;line-height:12px;color:var(--orange-mid)}
.embrace{left:261px;top:285px;width:400px;height:275px;background:radial-gradient(ellipse at 45% 60%,#2c2b32 0%,#3a3840 35%,#7b7d8e 55%,rgba(235,200,190,.35) 80%,rgba(228,221,207,0) 100%)}
.every{position:absolute;left:105px;top:268px;font-family:var(--serif);font-size:14.5px;line-height:16.5px;color:var(--ink)}
</style>
</head>
<body>
<div class="canvas">

  <!-- Outside spread -->
  <section class="sheet sheet--outside">
    <div class="panel panel--left about">
      <div class="wordmark wordmark--white" style="left:70px;top:28px">
        <span class="wordmark__name">Willow Brook<br>Paddock Refuge</span>
        <span class="wordmark__square"></span>
      </div>
      <h2 class="about__title">About Us</h2>
      <div class="about__rule"></div>
      <p class="about__body">We're a peaceful haven for animals in need, primarily horses and ponies, but sometimes others find refuge here too. Many of our residents arrive in poor condition, requiring long-term rehabilitation and lifelong care. Some are aged, unsound, or otherwise unsuitable for adoption — yet still full of life and deserving of love.</p>
      <div class="about__addr">
        <svg width="9" height="12" viewBox="0 0 9 12"><path d="M4.5 1a3 3 0 0 1 3 3c0 2.2-3 5-3 5s-3-2.8-3-5a3 3 0 0 1 3-3z" fill="none" stroke="#FDF4ED" stroke-width="1.2"/><circle cx="4.5" cy="4" r="1" fill="#FDF4ED"/><line x1="1.5" y1="11" x2="7.5" y2="11" stroke="#FDF4ED"/></svg>
        [Address]
      </div>
      <p class="about__dgr">As a registered DGR* charity,<br>all donations over $2 are tax-deductible.</p>
    </div>

    <div class="panel panel--mid contact">
      <h2 class="contact__title">Ready to sponsor a life?</h2>
      <p class="contact__intro">Visit <span>[website URL]</span> to view animals available for sponsorship and choose the one that speaks to your heart.</p>
      <p class="contact__label">Contact us:</p>
      <ul class="contact__list">
        <li><svg width="13" height="13"><circle cx="6.5" cy="6.5" r="6.5" fill="#F08F49"/><path d="M4 3.5l1.3 1.6-.7.9a5 5 0 0 0 2.4 2.4l.9-.7 1.6 1.3-.8 1A5.5 5.5 0 0 1 3 4.3z" fill="#fff"/></svg>[Phone number]</li>
        <li><svg width="13" height="13"><circle cx="6.5" cy="6.5" r="6.5" fill="#F08F49"/></svg>[Social media]</li>
        <li><svg width="13" height="13"><circle cx="6.5" cy="6.5" r="6.5" fill="#F08F49"/></svg>[Social media]</li>
        <li><svg width="13" height="13"><circle cx="6.5" cy="6.5" r="6.5" fill="#F08F49"/><path d="M6.5 3a2 2 0 0 1 2 2c0 1.5-2 3.5-2 3.5s-2-2-2-3.5a2 2 0 0 1 2-2z" fill="#fff"/></svg>[Location]</li>
      </ul>
      <div class="photo pony" role="img" aria-label="Palomino pony standing on a log"></div>
    </div>

    <div class="photo herd" role="img" aria-label="Herd of horses running across a grassy paddock with gum trees behind"></div>

    <div class="panel panel--right cover">
      <div class="photo mares" role="img" aria-label="Two bay horses standing together, one wearing a rug"></div>
      <h1 class="cover__title">Be Their<br>Safe Place.</h1>
      <div class="cover__rule"></div>
      <p class="cover__text">Support rescued horses and animals with us at Willow Brook Paddock Refuge.</p>
      <div class="wordmark wordmark--white" style="left:100px;top:477px">
        <span class="wordmark__name">Willow Brook<br>Paddock Refuge</span>
        <span class="wordmark__square"></span>
      </div>
    </div>
  </section>

  <!-- Inside spread -->
  <section class="sheet sheet--inside">
    <div class="panel panel--left">
      <div class="photo donkey" role="img" aria-label="Grey donkey and pale foal beside a red gum tree"></div>
      <div class="wordmark wordmark--white" style="left:130px;top:336px">
        <span class="wordmark__name">Willow Brook<br>Paddock Refuge</span>
        <span class="wordmark__square"></span>
      </div>
      <div class="saves">
        <h2 class="saves__title">Your sponsorship saves lives.</h2>
        <div class="saves__body">
          <p>When you become a sponsor, you help us provide ongoing vet care, quality food, shelter, and emotional recovery for animals that have nowhere else to go. Your kindness ensures they live out their days in safety and peace.</p>
          <p>We offer two levels of sponsorship, both vital to our mission.</p>
        </div>
      </div>
    </div>

    <div class="panel panel--mid">
      <div class="tier__body">
        <ul class="tier__list">
          <li>Regular weekly donations ($15–$25,<br>based on the animal's needs)</li>
          <li>Receive a personalised e-certificate</li>
          <li>Six-monthly updates on your sponsored animal</li>
          <li>Optional private visit to meet your horse or pony</li>
        </ul>
        <p class="tier__note">Your support helps cover the day-to-day costs of care and lets us plan for the future.</p>
      </div>
      <div class="tier__head tier__head--keepers">
        <div class="tier__icon"></div>
        <h3 class="tier__title">Keepers of WBPR</h3>
        <div class="tier__rule"></div>
        <p class="tier__sub">For those who want a deeper connection with our residents.</p>
      </div>
    </div>

    <div class="panel panel--right">
      <div class="tier__body">
        <ul class="tier__list">
          <li>Flexible donation options</li>
          <li>Perfect for gifts, schools, or one-time supporters</li>
          <li>Still helps us provide food, vet care, and shelter</li>
          <li>A great introduction to rescue &amp; rehabilitation</li>
        </ul>
      </div>
      <div class="tier__head tier__head--allies">
        <div class="tier__icon"></div>
        <h3 class="tier__title">Allies of WBPR</h3>
        <div class="tier__rule"></div>
        <p class="tier__sub">For those who want to help,<br>can't commit long term.</p>
      </div>
    </div>

    <div class="photo embrace" role="img" aria-label="Dark horse resting its head against a person in jeans"></div>

    <div class="panel panel--right" style="background:none">
      <p class="every">Every donation<br>makes a difference,<br>no matter<br>the size or frequency.</p>
      <div class="wordmark wordmark--orange" style="left:136px;top:494px">
        <span class="wordmark__name" style="font-size:11px">Willow Brook<br>Paddock Refuge</span>
        <span class="wordmark__square" style="width:24px;height:40px"></span>
      </div>
    </div>
  </section>

</div>
</body>
</html>
```